Quorva - corporate Business Card

We need a good look and innovative business card for a new start up company based in Los Angeles called "Quorva". We are in a payment business, including payment card, app, and ewallet. We are expert in online payment and Card not present (CNP) transaction.
We need an innovative, modern business card.

Our logo font is Aero Matics

Target Market(s)

Startup - Bank - Online Payment - Card Manufacturing

Industry/Entity Type

Startup

Contact Information for Business Card

phone: 555 014 7396 - Address: 4172 Marlowe blvd, Fenwick Hills, OR 97299

Requirements
Must have
• Message: innovative, professional, expert, high tech, trust, online payment expert, security
Nice to have
• no comment
Should not have
• no Comment

```html
<!DOCTYPE html>
<html lang="en">
<head>
<meta charset="utf-8">
<title>Quorva – Business Card</title>
<link href="https://fonts.googleapis.com/css2?family=Open+Sans:wght@400;600;700&display=swap" rel="stylesheet">
<style>
  :root {
    --brand-red: #b81f2f;
    --card-white: #ffffff;
    --backdrop: #ecebea;
  }
  * { margin: 0; padding: 0; box-sizing: border-box; }
  html, body { width: 1200px; height: 900px; overflow: hidden; }
  body {
    position: relative;
    background: var(--backdrop);
    font-family: "Open Sans", Arial, sans-serif;
  }
  .card {
    position: absolute;
    background: var(--card-white);
    overflow: hidden;
    box-shadow: 0 6px 18px rgba(0,0,0,0.15);
  }
  .card--front { left: 77px; top: 33px; width: 590px; height: 365px; }
  .card--back  { left: 388px; top: 505px; width: 567px; height: 352px; }

  .band { position: absolute; left: 0; width: 100%; background: var(--brand-red); }
  .card--front .band { top: 60px; height: 230px; }
  .card--back .band--top { top: 0; height: 110px; }
  .card--back .band--bottom { top: 242px; height: 110px; }

  .contact { position: absolute; left: 31px; top: 81px; color: var(--card-white); }
  .contact__name { font-size: 21px; font-weight: 700; line-height: 1.2; }
  .contact__role { font-size: 15.5px; font-weight: 400; line-height: 1.3; }
  .contact__lines { margin-top: 30px; font-size: 15.5px; line-height: 22px; }
  .contact__line { display: flex; align-items: center; gap: 6px; }
  .contact__line svg { width: 12px; height: 12px; fill: var(--card-white); }
  .contact__address { margin-top: 24px; font-size: 15.5px; line-height: 21px; }

  .front-mark { position: absolute; left: 311px; top: 56px; width: 238px; height: 238px; }
  .front-mark__name {
    position: absolute; inset: 0;
    display: flex; align-items: center; justify-content: center;
    color: var(--card-white); font-size: 40px; font-weight: 600;
  }

  .brand-lockup {
    position: absolute; left: 106px; top: 120px; height: 112px;
    display: flex; align-items: center; gap: 16px;
  }
  .brand-lockup__dot { width: 112px; height: 112px; border-radius: 50%; background: var(--brand-red); }
  .brand-lockup__name { color: var(--brand-red); font-size: 62px; font-weight: 600; letter-spacing: 1px; }
</style>
</head>
<body>
  <section class="card card--front" aria-label="Business card front">
    <div class="band"></div>
    <div class="contact">
      <p class="contact__name">Daniel Reyes</p>
      <p class="contact__role">Managing Director</p>
      <div class="contact__lines">
        <p class="contact__line">
          <svg viewBox="0 0 24 24" aria-hidden="true"><path d="M6.6 10.8a15.1 15.1 0 0 0 6.6 6.6l2.2-2.2a1 1 0 0 1 1-.25 11.4 11.4 0 0 0 3.6.57 1 1 0 0 1 1 1V20a1 1 0 0 1-1 1A17 17 0 0 1 3 4a1 1 0 0 1 1-1h3.5a1 1 0 0 1 1 1c0 1.250.2 2.450.57 3.570a1 1 0 0 1-.25 1z"/></svg>
          555 014 7396
        </p>
        <p class="contact__line">
          <svg viewBox="0 0 24 24" aria-hidden="true"><path d="M12 2a10 10 0 1 0 0 20 10 10 0 0 0 0-20zm6.9 6h-2.9a15.6 15.6 0 0 0-1.4-3.6A8 8 0 0 1 18.9 8zM12 4a14 14 0 0 1 1.9 4h-3.8A14 14 0 0 1 12 4zM4.3 14a8 8 0 0 1 0-4h3.4a16 16 0 0 0 0 4zm.8 2h2.9a15.6 15.6 0 0 0 1.4 3.6A8 8 0 0 1 5.1 16zM8 8H5.1a8 8 0 0 1 4.3-3.6A15.6 15.6 0 0 0 8 8zm4 12a14 14 0 0 1-1.9-4h3.8A14 14 0 0 1 12 20zm2.3-6H9.7a14.7 14.7 0 0 1 0-4h4.6a14.7 14.7 0 0 1 0 4zm.3 5.6a15.6 15.6 0 0 0 1.4-3.6h2.9a8 8 0 0 1-4.3 3.6zM16.3 14a16 16 0 0 0 0-4h3.4a8 8 0 0 1 0 4z"/></svg>
          www.quorva.com
        </p>
      </div>
      <p class="contact__address">4172 Marlowe blvd,<br>Fenwick Hills, OR 97299</p>
    </div>
    <div class="front-mark">
      <svg width="238" height="238" viewBox="0 0 238 238" aria-hidden="true">
        <circle cx="119" cy="119" r="113" fill="none" stroke="#ffffff" stroke-width="12"/>
      </svg>
      <span class="front-mark__name">Quorva</span>
    </div>
  </section>

  <section class="card card--back" aria-label="Business card back">
    <div class="band band--top"></div>
    <div class="brand-lockup">
      <span class="brand-lockup__dot" aria-hidden="true"></span>
      <span class="brand-lockup__name">quorva</span>
    </div>
    <div class="band band--bottom"></div>
  </section>
</body>
</html>
```